Simple one page Wordpress website

We need a quick turnaround single page wordpress website.
The design needs to be very simple and clean.
We already have some design assets (logos and colours etc) and some draft copy for the page.

We need all the files for us to be able to create a wordpress site. We can do this ourselves and we will host it.

```html
<!DOCTYPE html>
<html lang="en">
<head>
<meta charset="utf-8">
<title>Fieldvet — Veterinary Diagnostics Platform</title>
<link href="https://fonts.googleapis.com/css2?family=Poppins:wght@400;500;600;700&display=swap" rel="stylesheet">
<style>
:root{
  --green:#86a81a;
  --forest:#2a3d33;
  --blue:#3b7fc1;
  --ink:#1e1e1e;
  --text:#555;
  --muted:#8a8a8a;
  --panel:#f5f5f5;
  --line:#e2e2e2;
  --white:#fff;
}
*{margin:0;padding:0;box-sizing:border-box}
html,body{width:1200px;height:3907px;overflow:hidden}
body{font-family:"Poppins",sans-serif;color:var(--text);background:var(--white);position:relative}
a{color:inherit;text-decoration:none}
.abs{position:absolute}
.rule{width:60px;height:3px;background:var(--green)}
.h2{font-family:"Poppins",sans-serif;font-weight:600;font-size:42px;color:var(--ink);line-height:1.15}

/* hero */
.hero{position:absolute;left:0;top:0;width:1200px;height:680px;overflow:hidden}
.hero-photo{position:absolute;inset:0;background:radial-gradient(ellipse at 60% 10%,#a0712e 0%,#5a4628 30%,#2d2a20 65%),linear-gradient(180deg,#3a3426,#6f6350);}
.hero-photo::after{content:"";position:absolute;inset:0;background:rgba(20,18,14,.35)}
.brand{position:absolute;left:110px;top:28px;color:var(--white);font-weight:600;font-size:40px;letter-spacing:2px}
.nav{position:absolute;right:112px;top:42px;display:flex;gap:20px;font-size:15px;color:var(--white)}
.nav .active{color:var(--green)}
.nav .login{display:flex;align-items:center;gap:6px}
.hero-title{position:absolute;top:228px;width:1200px;text-align:center;color:var(--white);font-weight:600;font-size:60px}
.hero-lede{position:absolute;top:308px;left:325px;width:550px;text-align:center;color:var(--white);font-size:14px;line-height:29.5px}
.btn{display:flex;align-items:center;justify-content:center;background:var(--forest);color:var(--white);font-weight:600;font-size:14px}
.hero .btn{position:absolute;left:505px;top:413px;width:191px;height:51px}
.hero-curve{position:absolute;left:0;top:560px}
.scroll-down{position:absolute;left:578px;top:627px;width:45px;height:45px;border-radius:50%;background:var(--white);box-shadow:0 2px 8px rgba(0,0,0,.2);display:flex;align-items:center;justify-content:center}

/* mission */
.mission-title{top:748px;width:1200px;text-align:center}
.mission .rule{left:570px;top:812px}
.mission-text{top:830px;left:180px;width:840px;text-align:center;font-size:14px;line-height:29px;color:#444}

/* capabilities */
.cap-panel{left:0;top:1092px;width:824px;height:531px;background:var(--panel)}
.cap-photo{left:599px;top:982px;width:601px;height:470px;background:linear-gradient(135deg,#6d8b3f 0%,#8a5a33 35%,#c9b9a2 55%,#6f8f48 80%,#4a6a2c 100%)}
.cap-note{left:599px;top:1377px;width:601px;height:75px;background:rgba(25,25,25,.72);color:var(--white);font-size:13.5px;line-height:24px;padding:12px 28px}
.cap-note a{color:var(--green);text-decoration:underline}
.cap-title{left:111px;top:1126px}
.cap .rule{left:111px;top:1192px}
.cap-copy{left:111px;top:1210px;width:440px;font-size:12px;line-height:24px;color:#666}
.cap-copy p{margin-bottom:8px}
.cap-sub{color:var(--blue);font-weight:500;font-size:15.5px;line-height:29px;margin:10px 0 6px}
.cap-list{left:111px;top:1515px;width:560px;display:grid;grid-template-columns:380px 180px;font-size:12px;color:#444;list-style:none;row-gap:5px}
.cap-list li{display:flex;align-items:center;gap:10px}
.cap-list li::before{content:"→";color:var(--blue);font-size:13px}

/* venture */
.ven-title{left:111px;top:1725px}
.ven .rule{left:111px;top:1834px}
.contact-row{left:111px;display:flex;align-items:center;gap:18px;font-size:14px;color:#666}
.contact-row strong{font-weight:400;font-size:21px;color:var(--ink)}
.bubble{width:70px;height:70px;border-radius:50%;background:var(--green);display:flex;align-items:center;justify-content:center;box-shadow:0 4px 8px rgba(0,0,0,.15)}
.ven-copy{left:599px;top:1712px;width:480px;font-size:12px;line-height:25.8px;color:#666}
.ven-copy p{margin-bottom:19px}

/* team */
.team-title{top:2165px;width:1200px;text-align:center}
.team .rule{left:565px;top:2222px;width:70px}
.card{top:2259px;width:317px;height:408px;border:1px solid var(--line);background:var(--white);text-align:center}
.card-photo{margin:9px 9px 0;height:274px;background:linear-gradient(160deg,#cfcac2,#9c948a)}
.card:nth-child(2) .card-photo{background:linear-gradient(160deg,#d8d8d8,#a9a9a9)}
.card:nth-child(3) .card-photo{background:linear-gradient(160deg,#d6dadb,#a6b0b3)}
.card-name{margin-top:14px;font-weight:500;font-size:15px;color:var(--ink)}
.card-role{font-size:13px;color:var(--muted);margin-top:1px}
.card-social{display:flex;justify-content:center;gap:10px;margin-top:14px}
.card-social span{width:34px;height:34px;border:1px solid var(--line);display:flex;align-items:center;justify-content:center}
.card-social span::after{content:"";width:8px;height:8px;border-radius:50%;background:var(--green)}
.dots{top:2704px;left:570px;display:flex;gap:4px}
.dots span{width:12px;height:12px;border-radius:50%;border:1.5px solid #555}
.dots span.on{border-color:var(--blue)}

/* contact */
.touch-panel{left:0;top:2803px;width:824px;height:531px;background:var(--panel)}
.touch-title{left:111px;top:2892px}
.touch .rule{left:111px;top:2958px}
.touch-text{left:111px;top:2975px;width:440px;font-size:12px;line-height:27.6px;color:#666}
.touch .btn{position:absolute;left:111px;top:3184px;width:193px;height:51px}
.news{left:627px;top:2900px;width:573px;height:337px;background:linear-gradient(135deg,#3f5a46,#2f4a38 60%,#40594a);color:var(--white);padding:28px 48px 0 26px}
.news-kicker{font-size:12px;font-weight:600;color:var(--green);margin-left:5px}
.news-title{font-size:31px;font-weight:500;margin-top:8px}
.news .rule{margin:10px 0 0 5px;width:76px}
.news-text{font-size:13.5px;line-height:28px;margin-top:18px;color:#e9ede9}
.news-field{margin-top:16px;width:496px;height:58px;border:1px solid rgba(255,255,255,.8);display:flex;align-items:center;justify-content:space-between;padding:0 12px 0 14px;font-size:13.5px}
.news-send{width:28px;height:28px;border-radius:50%;background:var(--white);display:flex;align-items:center;justify-content:center}

/* footer */
.foot-brand{top:3390px;width:1200px;text-align:center;font-weight:600;font-size:92px;color:var(--blue);letter-spacing:6px;line-height:1.1}
.foot-col{top:3537px}
.foot-col h4{font-size:15px;font-weight:600;color:var(--ink);letter-spacing:.3px}
.foot-col .rule{width:30px;height:2px;background:#333;margin:12px 0 16px}
.foot-col ul{list-style:none;font-size:14px;color:#444}
.foot-col li{line-height:30px}
.foot-contact dt{font-size:13.5px;color:#333;margin-top:8px;font-weight:500}
.foot-contact dt:first-child{margin-top:0}
.foot-contact dd{font-size:13px;color:#444;line-height:23px;display:flex;gap:6px}
.foot-contact dd svg{flex:none;margin-top:5px}
.foot-about{font-size:13px;line-height:26px;color:#555}
.foot-rule{left:110px;top:3814px;width:980px;height:1px;background:var(--line)}
.copyright{left:116px;top:3850px;font-size:14px;color:#333}
.foot-social{left:962px;top:3852px;display:flex;gap:14px}
.foot-social span{width:18px;height:18px;border-radius:50%;background:#333}
</style>
</head>
<body>

<header class="hero">
  <div class="hero-photo" role="img" aria-label="Photo of a veterinarian with a stethoscope tending a brown and white horse in a sunlit paddock"></div>
  <div class="brand">FIELDVET</div>
  <nav class="nav">
    <a class="active" href="#">Home</a>
    <a href="#mission">Mission</a>
    <a href="#capabilities">Capabilities</a>
    <a href="#venture">Venture</a>
    <a href="#team">Team</a>
    <a class="login" href="#"><svg width="14" height="14" viewBox="0 0 14 14"><circle cx="7" cy="7" r="6" fill="none" stroke="#86a81a" stroke-width="1.3"/><circle cx="7" cy="5.5" r="2" fill="#86a81a"/><path d="M3.5 11a4 3 0 0 1 7 0" fill="#86a81a"/></svg>Login</a>
  </nav>
  <h1 class="hero-title">Fieldvet</h1>
  <p class="hero-lede">Fieldvet is deploying a Software as a Service (SaaS) platform to facilitate the efficient collection, transmission, secure storage and anonymised analysis of data integral to animal diagnostics.</p>
  <a class="btn" href="#">Get Started</a>
  <svg class="hero-curve" width="1200" height="120" viewBox="0 0 1200 120">
    <path d="M0 24 Q600 140 1200 24 V120 H0Z" fill="#86a81a"/>
    <path d="M0 30 Q600 162 1200 26 V120 H0Z" fill="#fff"/>
  </svg>
  <span class="scroll-down"><svg width="12" height="8" viewBox="0 0 12 8"><path d="M1 1 L6 7 L11 1Z" fill="#333"/></svg></span>
</header>

<section class="mission" id="mission">
  <h2 class="abs h2 mission-title">Mission</h2>
  <div class="abs rule"></div>
  <p class="abs mission-text">Fieldvet is deploying a Software as a Service (SaaS) platform to facilitate the efficient collection, transmission, secure storage and anonymised analysis of data integral to animal diagnostics</p>
</section>

<section class="cap" id="capabilities">
  <div class="abs cap-panel"></div>
  <div class="abs cap-photo" role="img" aria-label="Photo of a smiling vet with a clipboard standing beside a chestnut horse among trees"></div>
  <p class="abs cap-note">Interested parties seeking further information should contact us at<br><a href="#">hello@fieldvet.example</a></p>
  <h2 class="abs h2 cap-title">Capabilities</h2>
  <div class="abs rule"></div>
  <div class="abs cap-copy">
    <p>Originally developed for the human market, the core platform has been deployed in the UK and Ireland and has been used to securely process nearly 3 million cases</p>
    <p>The platform has been widely used by leading pharmacies, employers, public health services and of the UK's largest private sector laboratories</p>
    <h3 class="cap-sub">Turnkey Initial Veterinary Deployment – Animal Health and Welfare Pathway</h3>
    <p>Fieldvet is finalising the design of a bespoke platform to facilitate the collection and processing of data and tests for the Animal Health and Welfare Pathway. Key elements include</p>
  </div>
  <ul class="abs cap-list">
    <li>Facilitated data collection at the farm by vets</li>
    <li>Invoice support</li>
    <li>Secure and efficient processing of test samples by labs</li>
    <li>Data analysis reporting</li>
    <li>Digital results reporting</li>
  </ul>
</section>

<section class="ven" id="venture">
  <h2 class="abs h2 ven-title">Fieldvet is a joint<br>venture between</h2>
  <div class="abs rule"></div>
  <div class="abs contact-row" style="top:1878px">
    <span class="bubble"><svg width="26" height="26" viewBox="0 0 24 24"><path d="M6.6 10.8a15 15 0 0 0 6.6 6.6l2.2-2.2a1 1 0 0 1 1-.25 11.4 11.4 0 0 0 3.6.6 1 1 0 0 1 1 1V20a1 1 0 0 1-1 1A17 17 0 0 1 3 4a1 1 0 0 1 1-1h3.5a1 1 0 0 1 1 1c0 1.25.2 2.45.6 3.6a1 1 0 0 1-.25 1z" fill="#fff"/></svg></span>
    <span>Call Now - <strong>+1 555 014 2290</strong></span>
  </div>
  <div class="abs contact-row" style="top:1963px">
    <span class="bubble"><svg width="28" height="22" viewBox="0 0 28 22"><rect x="1" y="1" width="26" height="20" rx="2" fill="#fff"/><path d="M2 3 L14 12 L26 3" fill="none" stroke="#86a81a" stroke-width="2"/></svg></span>
    <span>Email Us - <strong>hello@fieldvet.example</strong></span>
  </div>
  <div class="abs ven-copy">
    <p>Ridgeway Farm Health Ltd (RFH), an innovative veterinary-led, close to market sustainable food research organisation. RFH brings together a team of highly experienced vets representing key opinion leaders within the livestock industry and additional technical support staff through its shareholder practice Millbrook Veterinary Group, Yorkshire. Millbrook is a 75 year old six centre veterinary group in North Yorkshire, focusing on livestock and equine. In turn Millbrook is part of FarmVets Alliance, an independent grouping of 40+ Farm and Equine practices across the UK</p>
    <p>Tailored Diagnostics Limited (TDL), is a rapidly growing Software as a Service platform provider in the digital health market. TDL deploys its agile and collaborative software development process working in partnership with its clients, using the skills of both parties to build the best solutions as effectively and efficiently as possible. Its clients include some of the country's largest pharmacies, employers and laboratories</p>
  </div>
</section>

<section class="team" id="team">
  <h2 class="abs h2 team-title">Meet The Team</h2>
  <div class="abs rule"></div>
  <div>
    <article class="abs card" style="left:112px">
      <div class="card-photo" role="img" aria-label="Portrait of a team member in a yellow blouse in an office"></div>
      <h3 class="card-name">Mara Vandell</h3><p class="card-role">Lorem ipsum</p>
      <div class="card-social"><span></span><span></span></div>
    </article>
    <article class="abs card" style="left:441px">
      <div class="card-photo" role="img" aria-label="Portrait of a team member in a navy sweater"></div>
      <h3 class="card-name">Mara Vandell</h3><p class="card-role">Lorem ipsum</p>
      <div class="card-social"><span></span><span></span></div>
    </article>
    <article class="abs card" style="left:771px">
      <div class="card-photo" role="img" aria-label="Portrait of a team member in an olive top"></div>
      <h3 class="card-name">Mara Vandell</h3><p class="card-role">Lorem ipsum</p>
      <div class="card-social"><span></span><span></span></div>
    </article>
  </div>
  <div class="abs dots"><span></span><span class="on"></span><span></span><span></span></div>
</section>

<section class="touch">
  <div class="abs touch-panel"></div>
  <h2 class="abs h2 touch-title">Get In Touch</h2>
  <div class="abs rule"></div>
  <p class="abs touch-text">Lorem ipsum dolor sit amet, consectetur adipiscing elit, sed do eiusmod tempor incididunt ut labore et dolore magna aliqua. Ut enim ad minim veniam, quis nostrud exercitation ullamco laboris nisi ut aliquip ex ea commodo consequat. Duis aute irure dolor in reprehenderit in voluptate velit esse cillum dolore eu fugiat nulla pariatur. Excepteur sint occaecat cupidatat non proident, sunt in culpa qui officia deserunt mollit anim id est laborum</p>
  <a class="btn" href="#">Contact Us</a>
  <div class="abs news" role="group" aria-label="Newsletter signup over a muted photo of a vet with animals">
    <p class="news-kicker">SUBSCRIBE US</p>
    <h3 class="news-title">Join Our Newsletter</h3>
    <div class="rule"></div>
    <p class="news-text">Lorem ipsum dolor sit amet, consectetur adipiscing elit, sed do eiusmod tempor incididunt ut labore et dolore magna</p>
    <div class="news-field"><span>Enter Your Email</span><span class="news-send"><svg width="14" height="14" viewBox="0 0 14 14"><path d="M1 6.5 L13 1 L8 13 L6.5 8Z" fill="#2a3d33"/></svg></span></div>
  </div>
</section>

<footer>
  <div class="abs foot-brand">FIELDVET</div>
  <div class="abs foot-col" style="left:114px">
    <h4>QUICK LINKS</h4><div class="rule"></div>
    <ul><li>Home</li><li>Mission</li><li>Capabilities</li><li>Venture</li><li>Team</li></ul>
  </div>
  <div class="abs foot-col" style="left:290px">
    <h4>SUPPORT</h4><div class="rule"></div>
    <ul><li>Information</li><li>Privacy Policy</li><li>Terms &amp; Conditions</li></ul>
  </div>
  <div class="abs foot-col" style="left:498px;width:220px">
    <h4>CONTACT US</h4><div class="rule"></div>
    <dl class="foot-contact">
      <dt>ADDRESS</dt>
      <dd><svg width="8" height="11" viewBox="0 0 8 11"><path d="M4 0a4 4 0 0 1 4 4c0 3-4 7-4 7S0 7 0 4a4 4 0 0 1 4-4z" fill="#3b7fc1"/><circle cx="4" cy="4" r="1.4" fill="#fff"/></svg><span>Lorem ipsum dolor sit amet, consectetur adipiscing</span></dd>
      <dt>PHONE</dt>
      <dd><svg width="10" height="10" viewBox="0 0 24 24"><path d="M6.6 10.8a15 15 0 0 0 6.6 6.6l2.2-2.2a1 1 0 0 1 1-.25 11.4 11.4 0 0 0 3.6.6 1 1 0 0 1 1 1V20a1 1 0 0 1-1 1A17 17 0 0 1 3 4a1 1 0 0 1 1-1h3.5a1 1 0 0 1 1 1c0 1.25.2 2.45.6 3.6a1 1 0 0 1-.25 1z" fill="#3b7fc1"/></svg><span>+1 555-014-2290</span></dd>
      <dt>EMAIL</dt>
      <dd><svg width="12" height="9" viewBox="0 0 12 9"><rect width="12" height="9" rx="1" fill="#3b7fc1"/><path d="M1 1 L6 5 L11 1" fill="none" stroke="#fff"/></svg><span>hello@fieldvet.example</span></dd>
    </dl>
  </div>
  <div class="abs foot-col" style="left:766px;width:320px">
    <h4>ABOUT</h4><div class="rule"></div>
    <p class="foot-about">Lorem ipsum dolor sit amet,adipiscing elit, sed do eiusmod tempor incididunt dolore magna aliqua. Ut enim ad minim veniam, quis nostrud exercitation ullamco laboris nisi ut aliquip ex ea commodo consequat.</p>
  </div>
  <div class="abs foot-rule"></div>
  <p class="abs copyright">© 2022 &nbsp; All Rights Reserved</p>
  <div class="abs foot-social"><span></span><span></span><span></span><span></span></div>
</footer>

</body>
</html>
```